Corporate website design needed

We need a Contemporary Industrial/Tech/Logistics Website design to match our logistic client's business. Our client consults and build logistics solutions that they manage but they are not a typical 3PL (3rd party logistics company) which is primarily engaged in moving boxes.
PSD file only for now, home and default templates.
COMPANY CHARACTER
DESIGN LOOK AND FEEL
• The design should also be modern and visually well organized — employing a combination of visual devices and info graphics. Keep it light and not too heavy but strong/ professional. And unique.
• The design should go beyond the typical industrial pick and pack 3PL representing [Logistics Company] as a High Tech/IT logistics company.
Some examples although these are not right for this client because they have much more content and present themselves more as a 3pl.
http://www.vobrelink-hub.example/ (More right then wrong - Like this but simplified)
http://www.durmaxfreight.example (Ugly)
http://www.tpwallerton.example (More right then wrong but different focus)
http://www.pelhamrye.example/ Too 3PL trucking… We want a bit ore high level approach
The difference, the design should be a fusion in core concepts that culminate in a design which implies the following attributes. Tech (Big data / analytics / software), Consultancy (Solutions, SME, Leader), 3PL Industry vertical solutions.
NOTE: The visualization of “tech” is not “1” and “0”, but more “software and analytics” Perhaps more like www.navimetra.example.
• They need to be seen as a solutions provider in Logistics and as in Subject matter experts
TONE
The tone needs to exude professionalism, expertise, though leadership along with technical and executional excellence.
Experienced
Knowledgeable
Confident
Determined
Straightforward
WEBSITE OBJECTIVES
• Focus C-Suite executives and logistics managers’ attention on [Logistics Company]s commanding knowledge and expertise, and unique approach to supply chain solutions producing more RFP wins
• Create an easy to scan design which decreases the reliance on text through featured text, summaries, and smaller “chunked” size bits of information.
• Convey [Logistics Company] as high-tech 3PL solutions developer and services provider with a ‘high-touch’ consultative approach.
• Showcase [Logistics Company]’s value propositions. (See Slider Content)
• Showcase [Logistics Company]’s expertise in logistical analytics.
• Gain recognition as an industry leader in evolutionary new space (supply chain 2.0)
WEBSITE STRATEGY
• Reduce reliance on text (at least within initial entry points for each section)
• Typography: Watch text line lengths and readability, bolder fonts. NO SERIFS
• Generally, create a click-through format so that users who want more details can find it, and those who don’t can get a snapshot without clicking through.
• Increase visual content through info graphics and some dynamic content, photography
• Better utilize the space on each page (e.g., add visual interest, photography and iconography where appropriate to break up copy blocks and maintain readable line lengths).
COLOR SCHEME
• Create a more engaging color scheme (the logo will remain the same under all circumstances).
• Red / grayscale may work…. Not too dark or heavy. Not too much red. Ex. quiltora.example
• Also try blues and greys. They seem to like that. Open to suggestions but don’t get to crazy. Red is in their logo but too much may be a problem.
PHOTOGRAPHY
Yes. And I will upload some.
If you pick photography please be sure to note Which stock house used and the image number!
CONTENT
The content will be presented in a more hierarchical format — with lead-ins, paragraph and section headers and navigational cues to expand lengthier content allowing the visitor to more easily scan the website. No case studies, No Social media, News while on the home page should not be over emphasized. They don't post a lot so it gets dated quickly ...
I will be uploading a wire frame and other elements.
NOTE: I uploaded my EXAMPLE mock up which is close but not close enough.
I am not a great designer. So I am looking for an alternative that exceed my design ability! These examples show the basic layout but I really want some varied alternatives.
The colors are inconsistent and type not quite right. The grey bar at top is not right and should probably go away.
Please pull the basic elements in the example together into a great design.
If you have questions please contact me.
i will upload some photography tomorrow that may be of use.
Thanks!
Updates
Hi All,
We are still evaluating the submitted designs. Sorry for the delay.
Target Market(s)
This website is primarily a validation website. Few new customers will search and find them as such...
The site should be Focused on C-Suite executives and logistics managers’ attention on [Logistics Company]s commanding knowledge and expertise, and unique approach to supply chain solutions producing more RFP wins
Industry/Entity Type
Business
Font styles to use
Requirements
Must have
- Slide show, Clearly explain who they are and what they do.
Create an easy to scan design which decreases the reliance on text through featured text, summaries, and smaller “chunked” size bits of information.
Convey [Logistics Company] as high-tech 3PL solutions developer and services
provider with a ‘high-touch’ consultative approach.
Should not have
- No Ads space
No Social media
Not too cluttered. Keep it clean.

```html
<!DOCTYPE html>
<html lang="en">
<head>
<meta charset="utf-8">
<title>Veltrane Logistics</title>
<link href="https://fonts.googleapis.com/css2?family=Open+Sans:wght@400;600;700&display=swap" rel="stylesheet">
<style>
:root{
  --blue:#1772b0;
  --blue-deep:#0d4f86;
  --footer-blue:#0f6eab;
  --bar:#4a4f56;
  --panel:#1f2a35;
  --tab:#2e3135;
  --red:#c8102e;
  --yellow:#f7c600;
  --ink:#2c2c2c;
  --muted:#8a8a8a;
  --soft:#f3f3f3;
  --line:#dcdcdc;
  --night:#1c2b3a;
}
*{box-sizing:border-box;margin:0;padding:0}
html,body{width:720px;height:1200px;overflow:hidden}
body{font-family:"Open Sans",Arial,sans-serif;color:var(--ink);background:#fff;position:relative}
.abs{position:absolute}
.site-header{position:absolute;left:0;top:0;width:720px;height:60px;background:#fff}
.brand{position:absolute;left:66px;top:18px;display:flex;align-items:center;gap:8px}
.brand-dot{width:22px;height:22px;border-radius:50%;background:var(--red)}
.brand-name{font-size:11px;font-weight:600;letter-spacing:3px;color:#222;text-transform:uppercase;line-height:1.2}
.main-nav{position:absolute;right:66px;top:26px;display:flex;gap:12px;font-size:10px;color:#333}
.util-bar{position:absolute;top:60px;left:0;width:720px;height:25px;background:linear-gradient(#555a61,#3f444a)}
.sales{position:absolute;left:68px;top:6px;color:#fff;font-size:9.5px;display:flex;align-items:center;gap:4px}
.search{position:absolute;left:481px;top:3px;width:151px;height:19px;background:#fff;border:1px solid #ccc;font-size:7.5px;color:#999;padding:4px 6px}
.search-btn{position:absolute;left:632px;top:3px;width:21px;height:19px;background:var(--red);display:flex;align-items:center;justify-content:center}
.hero{position:absolute;top:85px;left:0;width:720px;height:264px;background:radial-gradient(ellipse at 50% 40%,#2a8fd0,#12609e 75%)}
.slide-panel{position:absolute;left:66px;top:150px;width:588px;height:180px;background:linear-gradient(90deg,#16324e,#1b3f60 60%,#173553);border-radius:4px 4px 0 0}
.device{position:absolute;left:106px;top:110px;width:267px;height:220px;background:#111;border-radius:12px 12px 0 0;border:2px solid #aaa;border-bottom:none}
.device-screen{position:absolute;left:137px;top:145px;width:205px;height:185px;background:linear-gradient(135deg,#e4e8ec,#7a98b4 55%,#2b3442)}
.slide-title{position:absolute;left:383px;top:164px;color:#fff;font-size:21px;font-weight:600}
.slide-sub{position:absolute;left:383px;top:190px;color:#e3ecf3;font-size:12px}
.slide-text{position:absolute;left:383px;top:219px;width:260px;color:#fff;font-size:8.6px;line-height:12px}
.btn-yellow{position:absolute;left:383px;top:283px;width:82px;height:22px;border-radius:11px;background:linear-gradient(#ffd938,#f1b800);color:#222;font-size:9.5px;display:flex;align-items:center;justify-content:center}
.arrow{position:absolute;top:252px}
.service-tabs{position:absolute;left:66px;top:330px;width:588px;height:49px;background:linear-gradient(#3a3d42,#25282c);display:flex;border-radius:0 0 4px 4px;box-shadow:0 12px 14px -6px rgba(0,0,0,.3)}
.tab{display:flex;align-items:center;justify-content:center;gap:8px;color:#fff;font-size:8.3px;font-weight:600;text-transform:uppercase;text-align:center;line-height:11px;border-right:1px solid #55585d}
.tab:last-child{border-right:none}
.difference-photo{position:absolute;left:66px;top:445px;width:176px;height:107px;background:linear-gradient(#b9c3cc,#6c7580 60%,#d8d2c6)}
.person-photo{position:absolute;left:242px;top:410px;width:62px;height:156px;background:linear-gradient(#cfd3d8,#24303f 35%,#1c2430)}
.section-title{position:absolute;font-size:14px;color:#222}
.body-copy{position:absolute;font-size:7.8px;line-height:12px;color:var(--muted)}
.btn-red{position:absolute;left:317px;top:538px;width:68px;height:19px;background:var(--red);color:#fff;font-size:8.5px;display:flex;align-items:center;justify-content:center;border-radius:2px}
.rule{position:absolute;height:1px;background:var(--line)}
.industry-card{position:absolute;top:628px;width:186px;height:137px;border-bottom:2px solid #ccc;background:var(--soft)}
.industry-card.active{border-bottom-color:var(--red)}
.industry-img{height:99px}
.industry-cap{text-align:center;font-size:11px;line-height:12px;color:#333;padding-top:9px}
.news-band{position:absolute;top:781px;left:0;width:720px;height:229px;background:var(--soft)}
.news-item{position:absolute;left:69px;width:302px}
.date{position:absolute;left:0;top:0;width:35px;height:42px;text-align:center}
.date .d{background:var(--red);color:#fff;font-size:12px;height:21px;line-height:21px}
.date .m{background:#e2e2e2;color:#444;font-size:10px;height:21px;line-height:21px}
.news-title{position:absolute;left:46px;top:3px;font-size:10px;color:#222}
.news-copy{position:absolute;left:46px;top:17px;width:256px;font-size:7.6px;line-height:12px;color:var(--muted)}
.video{position:absolute;left:392px;top:821px;width:255px;height:163px;background:linear-gradient(#c7d4df,#8b9aa8 40%,#2a2f36 70%,#4a6a86)}
.video-bar{position:absolute;left:0;bottom:0;width:100%;height:13px;background:#111}
.site-footer{position:absolute;top:1010px;left:0;width:720px;height:168px;background:var(--footer-blue)}
.footer-col{position:absolute;top:30px;color:#fff}
.footer-col h3{font-size:12px;font-weight:600;text-transform:uppercase;margin-bottom:8px}
.footer-col li{list-style:none;font-size:8px;line-height:12px}
.footer-brand{display:flex;align-items:center;gap:6px;margin:3px 0 14px}
.footer-brand span:first-child{width:16px;height:16px;border-radius:50%;border:2px solid #fff}
.footer-brand span:last-child{font-size:7px;letter-spacing:2px;text-transform:uppercase}
.footer-about{font-size:8px;line-height:10.7px;width:130px}
.bottom-bar{position:absolute;top:1178px;left:0;width:720px;height:22px;background:var(--night);color:#fff;font-size:7.8px}
.bottom-bar .copy{position:absolute;left:67px;top:6px}
.bottom-nav{position:absolute;right:65px;top:6px;display:flex;gap:7px}
.bottom-nav .on{color:#3aa0e8}
</style>
</head>
<body>
<header class="site-header">
  <div class="brand"><span class="brand-dot"></span><span class="brand-name">Veltrane<br>Logistics</span></div>
  <nav class="main-nav"><span>Home</span><span>Careers</span><span>Solutions</span><span>Our Process</span><span>Industries</span><span>Contact Us</span></nav>
</header>
<div class="util-bar">
  <div class="sales"><svg width="10" height="10" viewBox="0 0 10 10"><circle cx="5" cy="3" r="2.4" fill="#fff"/><path d="M0.5 10 Q5 4 9.5 10Z" fill="#fff"/></svg>Sales: 866-555-0182</div>
  <div class="search">Search</div>
  <div class="search-btn"><svg width="11" height="11" viewBox="0 0 11 11"><circle cx="4.5" cy="4.5" r="3.3" fill="none" stroke="#fff" stroke-width="1.5"/><path d="M7 7l3 3" stroke="#fff" stroke-width="1.6"/></svg></div>
</div>
<section class="hero">
</section>
<div class="slide-panel"></div>
<div class="device"></div>
<div class="device-screen" role="img" aria-label="Businessman touching a glowing interface of analytics icons"></div>
<h1 class="slide-title">A New Way To Think</h1>
<p class="slide-sub">About Supply Chain Transformation</p>
<p class="slide-text">Veltrane transforms supply chains by managing complexity, providing data-driven insights and implementing forward-thinking innovation and actionable strategies that change business results.</p>
<div class="btn-yellow">Read More</div>
<svg class="arrow" style="left:50px" width="16" height="22" viewBox="0 0 16 22"><path d="M12 2L4 11l8 9" fill="none" stroke="#fff" stroke-width="3"/></svg>
<svg class="arrow" style="left:654px" width="16" height="22" viewBox="0 0 16 22"><path d="M4 2l8 9-8 9" fill="none" stroke="#fff" stroke-width="3"/></svg>
<nav class="service-tabs">
  <div class="tab" style="width:145px"><svg width="18" height="18" viewBox="0 0 18 18"><circle cx="9" cy="9" r="6" fill="none" stroke="#fff" stroke-width="3" stroke-dasharray="3 2"/><circle cx="9" cy="9" r="2" fill="#fff"/></svg>Material Management<br>&amp; Factory Support</div>
  <div class="tab" style="width:151px"><svg width="20" height="14" viewBox="0 0 20 14"><circle cx="10" cy="7" r="6" fill="none" stroke="#fff" stroke-width="1.5"/><path d="M4 7h12M10 1v12" stroke="#fff"/></svg>Retail &amp; E-Commerce<br>Distribution</div>
  <div class="tab" style="width:143px"><svg width="16" height="16" viewBox="0 0 16 16"><path d="M2 2l12 12M14 2L2 14" stroke="#fff" stroke-width="2.4"/></svg>Aftermarket Support</div>
  <div class="tab" style="width:149px"><svg width="18" height="18" viewBox="0 0 18 18"><circle cx="9" cy="10" r="5" fill="none" stroke="#fff" stroke-width="3" stroke-dasharray="3 2"/><circle cx="14" cy="4" r="2.5" fill="#fff"/></svg>Critical Logistics</div>
</nav>

<div class="difference-photo" role="img" aria-label="Interior of a large industrial turbine hall"></div>
<div class="person-photo" role="img" aria-label="Businessman in a suit standing with arms crossed"></div>
<h2 class="section-title" style="left:315px;top:443px">The Veltrane Difference</h2>
<p class="body-copy" style="left:317px;top:466px;width:315px">Lorem Ipsum is simply dummy text of the printing and typesetting industry. Lorem Ipsum has been the industry's standard dummy text ever since the 1500s, when an unknown printer took a galley of type and scrambled it to make a type specimen book. It has survived not only five centuries, but also the leap into electronic typesetting, remaining essentially unchanged.</p>
<div class="btn-red">Read More</div>

<h2 class="section-title" style="left:66px;top:593px">Featured Industry</h2>
<div class="rule" style="left:66px;top:616px;width:588px"></div>
<div class="industry-card" style="left:66px"><div class="industry-img" role="img" aria-label="Engineer checking a control panel in a pipe plant" style="background:linear-gradient(90deg,#8a8f94,#d7dadd 60%,#9aa2a8)"></div><p class="industry-cap">Lorem ipsum dolor<br>sit amet.</p></div>
<div class="industry-card active" style="left:268px"><div class="industry-img" role="img" aria-label="Power station with smoking chimneys by the water" style="background:linear-gradient(#3f7fc4,#9bbfe0 50%,#5a6a4a 80%,#2f5f8a)"></div><p class="industry-cap">Lorem ipsum dolor<br>sit amet.</p></div>
<div class="industry-card" style="left:468px"><div class="industry-img" role="img" aria-label="Two workers in hard hats at a refinery" style="background:linear-gradient(#5f98d0,#9db6cc 50%,#3a4a66)"></div><p class="industry-cap">Lorem ipsum dolor<br>sit amet.</p></div>

<section class="news-band"></section>
<h2 class="section-title" style="left:66px;top:795px">Recent News</h2>
<span class="abs" style="left:345px;top:803px;font-size:7px;color:#333">View All</span>
<div class="rule" style="left:66px;top:815px;width:305px"></div>
<article class="news-item" style="top:828px">
  <div class="date"><div class="d">27</div><div class="m">Mar</div></div>
  <h3 class="news-title" style="font-weight:400">Lorem ipsum dolor sit amet</h3>
  <p class="news-copy">Lorem Ipsum is simply dummy text of the printing and typesetting industry. Lorem Ipsum has been the industry's standard dummy text ever since the 1500s, when an unknown printer took a galley of type and scrambled it to make a type specimen book.</p>
</article>
<div class="rule" style="left:66px;top:903px;width:305px"></div>
<article class="news-item" style="top:915px">
  <div class="date"><div class="d">27</div><div class="m">Mar</div></div>
  <h3 class="news-title" style="font-weight:400">Lorem ipsum dolor sit amet</h3>
  <p class="news-copy">Lorem Ipsum is simply dummy text of the printing and typesetting industry. Lorem Ipsum has been the industry's standard dummy text ever since the 1500s, when an unknown printer took a galley of type and scrambled it to make a type specimen book.</p>
</article>
<div class="video" role="img" aria-label="Video still of an offshore supply vessel at sea">
  <svg class="abs" style="left:110px;top:65px" width="34" height="34" viewBox="0 0 34 34"><circle cx="17" cy="17" r="17" fill="#111"/><path d="M13 10l11 7-11 7z" fill="#fff"/></svg>
  <div class="video-bar"><div class="abs" style="left:0;top:0;width:60px;height:2px;background:var(--red)"></div></div>
</div>

<footer class="site-footer">
  <div class="footer-col" style="left:68px"><h3>About Company</h3>
    <div class="footer-brand"><span></span><span>Veltrane Logistics</span></div>
    <p class="footer-about">Lorem ipsum dolor sit amet consectetur adipisicing elit eiusmod tempor incididunt ut labore et dolore magna aliqua ad minim veniam quis nostrud exercitation ullam.</p></div>
  <div class="footer-col" style="left:229px"><h3>Our Process</h3><ul><li>Concept of operations</li><li>Supplying the infrastructure</li><li>Analyzing the data</li><li>Managing complexity</li><li>Providing actionable strategies</li><li>Investing in our client's success</li><li>Driving business results</li></ul></div>
  <div class="footer-col" style="left:387px"><h3>Our Solutions</h3><ul><li>Business Analytics</li><li>Geographic Coverage</li><li>Project financing</li><li>Project implementation</li><li>Technology</li><li>Quality</li></ul></div>
  <div class="footer-col" style="left:531px"><h3>Industries We Serve</h3><ul><li>Aerospace</li><li>defense</li><li>Industrial</li><li>Manufacturing</li><li>Media and Entertainment</li><li>Medical</li><li>Retail</li><li>Telecom &amp; Electronics</li></ul></div>
</footer>
<div class="bottom-bar">
  <span class="copy">Copyright ©2014 Veltrane. All Rights Reserved.</span>
  <nav class="bottom-nav"><span class="on">Home</span>|<span>Careers</span>|<span>Solutions</span>|<span>Our Process</span>|<span>Industries</span>|<span>Contact Us</span></nav>
</div>
</body>
</html>
```